Business card for Sports Apparel business

DOUBLE SIDED DESIGN
We need business cards for a new sports apparel business. We are developing a protective headband for soccer initially.
Torvalle is focused on designing and developing head protection products to reduce the likelihood of concussion when playing sports. Exploring and understanding medical insights, material science research, current and former players experiences and governing bodies guidelines has allowed Torvalle to develop the safety, style, form and function requirements of a suitable product to bring to market.
Target Market(s)
Mums buying kits for the sons and daughters. Amateur footballers.
Industry/Entity Type
Sporting Good
Contact Information for Business Card
Martin Ashworth - CEO
Mobile: +44 7431589027
Email: martin@torvalle.co.uk
Tel: 0208 5519372
Helena Pargeter - COO
Mob: +44 7385 640117
Email: helena@torvalle.co.uk
Tel: 0208 5519372
Duncan Farrow - CCO
Mob: +44 7564 293081
Email: duncan@torvalle.co.uk
Tel: 0208 5519372
Look and feel
Each slider illustrates characteristics of the customer's brand and the style your logo design should communicate.

```html
<!DOCTYPE html>
<html lang="en">
<head>
<meta charset="utf-8">
<title>Torvalle Business Card</title>
<link rel="stylesheet" href="https://fonts.googleapis.com/css2?family=Montserrat:wght@300;400;600;700&display=swap">
<style>
  :root {
    --page: #2a2a2a;
    --card-grey: #676767;
    --brand-blue: #15599a;
    --white: #ffffff;
    --text-grey: #666666;
  }
  * { margin: 0; padding: 0; box-sizing: border-box; }
  html, body { width: 1200px; height: 900px; overflow: hidden; }
  body {
    background: var(--page);
    font-family: "Montserrat", sans-serif;
    position: relative;
  }
  .card {
    position: absolute;
    left: 250px;
    width: 700px;
    height: 400px;
    overflow: hidden;
  }
  .card-back {
    top: 30px;
    background: var(--card-grey);
    display: flex;
    align-items: center;
    justify-content: center;
  }
  .card-back .brand-name {
    color: var(--white);
    font-weight: 600;
    font-size: 66px;
    letter-spacing: 4px;
  }
  .card-front {
    top: 470px;
    background: var(--white);
  }
  .card-front .brand-name {
    position: absolute;
    left: 40px;
    top: 44px;
    color: var(--brand-blue);
    font-weight: 600;
    font-size: 38px;
    letter-spacing: 2px;
  }
  .person {
    position: absolute;
    right: 42px;
    top: 108px;
    text-align: right;
  }
  .person-name {
    color: var(--brand-blue);
    font-weight: 700;
    font-size: 21px;
    letter-spacing: 1.5px;
  }
  .person-role {
    color: var(--text-grey);
    font-weight: 400;
    font-size: 17px;
    letter-spacing: 1px;
    margin-top: 2px;
  }
  .wave {
    position: absolute;
    left: 0;
    top: 0;
    width: 700px;
    height: 400px;
  }
  .contacts {
    position: absolute;
    right: 42px;
    top: 262px;
    list-style: none;
    color: var(--white);
    font-weight: 300;
    font-size: 19px;
    line-height: 30px;
    text-align: right;
  }
  .contacts li {
    display: flex;
    align-items: center;
    justify-content: flex-end;
    gap: 14px;
  }
  .contacts svg { width: 18px; height: 18px; flex: none; }
</style>
</head>
<body>

<section class="card card-back">
  <span class="brand-name">TORVALLE</span>
</section>

<section class="card card-front">
  <span class="brand-name">TORVALLE</span>

  <div class="person">
    <p class="person-name">MARTIN ASHWORTH</p>
    <p class="person-role">CEO</p>
  </div>

  <svg class="wave" viewBox="0 0 700 400" aria-hidden="true">
    <path d="M0,354 C200,372 420,240 700,196 V400 H0 Z" fill="var(--card-grey)"/>
    <path d="M0,318 C220,362 430,214 700,170 V184 C430,228 220,378 0,334 Z" fill="var(--brand-blue)"/>
    <path d="M50,314 C200,344 330,340 470,318 C330,352 180,350 50,314 Z" fill="var(--brand-blue)"/>
  </svg>

  <ul class="contacts">
    <li>0208 551 9372
      <svg viewBox="0 0 18 18" fill="none" stroke="var(--white)" stroke-width="1.4"><rect x="5" y="1.5" width="8" height="15" rx="1.5"/><line x1="8" y1="14" x2="10" y2="14"/></svg>
    </li>
    <li>+44 7431589027
      <svg viewBox="0 0 18 18" fill="none" stroke="var(--white)" stroke-width="1.4"><path d="M4,2 L7,2 L8,6 L6,7.5 C7,10 8,11 10.5,12 L12,10 L16,11 L16,14 C16,15 15,16 14,16 C8,15.5 2.5,10 2,4 C2,3 3,2 4,2 Z"/></svg>
    </li>
    <li>martin@torvalle.co.uk
      <svg viewBox="0 0 18 18" fill="none" stroke="var(--white)" stroke-width="1.4"><rect x="1.5" y="4" width="15" height="10"/><path d="M1.5,4 L9,10 L16.5,4"/></svg>
    </li>
  </ul>
</section>

</body>
</html>
```